Vacation Rental Postcard Design

The Kingfisher's Perch is a vacation rental cottage. We want a postcard that can be used as promotional give-aways for visitors as well as something that can be given to the tourism board and local merchants to help us promote the rental.

Our tag line is" The Kingfisher's Perch - the finest perch on the ridge!". Should also include "Snohomish, WA USA"

We have also used "Come see what all of the buzz is about"

Want to include our info in small print on the mailing side portion of the postcard:

KLWT: www.klwtstays.example/417294
Chatterly: www.chatterly.example/thefinestperchontheridge

Target Market(s)

Couples, romantic, honeymooners, coming for wine tasting, hot air ballooning, hiking, enjoying nature

Industry/Entity Type

Tourism

```html
<!DOCTYPE html>
<html lang="en">
<head>
<meta charset="utf-8">
<title>The Kingfisher's Perch – Postcard Options</title>
<link rel="stylesheet" href="https://fonts.googleapis.com/css2?family=Bebas+Neue&family=Open+Sans:wght@400;600&display=swap">
<style>
  :root {
    --ink: #111111;
    --paper: #ffffff;
    --rule: #6e6e6e;
    --faint: #d9d9d9;
    --faint-ink: #c4c4c4;
    --shadow: rgba(0, 0, 0, 0.35);
  }
  html, body {
    margin: 0;
    padding: 0;
    overflow: hidden;
    background: var(--paper);
  }
  .board {
    position: relative;
    width: 1200px;
    height: 584px;
    overflow: hidden;
    background: var(--paper);
    font-family: "Open Sans", Arial, sans-serif;
    color: var(--ink);
  }
  .section-title {
    position: absolute;
    margin: 0;
    font-family: "Bebas Neue", Impact, sans-serif;
    font-weight: 400;
    font-size: 76px;
    line-height: 1;
    letter-spacing: 1px;
    writing-mode: vertical-rl;
    transform: rotate(180deg);
    color: var(--ink);
  }
  .section-title--back { left: 10px; top: 130px; }
  .section-title--front { left: 617px; top: 38px; }

  .card {
    position: absolute;
    background: var(--paper);
    box-shadow: 2px 3px 5px var(--shadow);
    overflow: hidden;
  }
  .card > * { position: absolute; }

  .photo { display: block; }
  .photo--sunset { background: linear-gradient(180deg, #c7597a 0%, #e8857a 55%, #3d3550 100%); }
  .photo--lounge { background: linear-gradient(160deg, #a66f3a 0%, #d9b47e 55%, #5a3a22 100%); }
  .photo--bedroom { background: linear-gradient(180deg, #a88a6a 0%, #e0d6c8 60%, #8a6a52 100%); }
  .photo--house { background: linear-gradient(180deg, #6f9fd3 0%, #2f6a4c 45%, #8a5a3a 100%); }
  .photo--meadow { background: linear-gradient(180deg, #7f8fb4 0%, #a8b3c8 45%, #5e8a3c 100%); }
  .photo--balloons { background: linear-gradient(180deg, #9ec1e0 0%, #c9794a 60%, #4e6e3a 100%); }
  .photo--autumn { background: linear-gradient(160deg, #88a6c8 0%, #c98a2e 55%, #6f8c46 100%); }
  .photo--garden { background: linear-gradient(180deg, #5e8a6a 0%, #8fb56a 50%, #3c5a3a 100%); }

  .stamp-box {
    width: 30px;
    height: 38px;
    border: 1px solid var(--ink);
    box-sizing: border-box;
  }
  .address-line {
    height: 1px;
    background: var(--rule);
  }
  .writing-lines {
    background: repeating-linear-gradient(to bottom, transparent 0 8px, var(--rule) 8px 9px);
  }
  .signature-line {
    height: 1px;
    background: var(--rule);
  }

  .emblem {
    display: flex;
    align-items: center;
    justify-content: center;
  }
  .emblem__circle {
    position: absolute;
    inset: 0;
    border-radius: 50%;
    background: var(--faint);
    opacity: 0.55;
  }
  .emblem__name {
    position: relative;
    font-family: "Bebas Neue", Impact, sans-serif;
    font-size: 22px;
    line-height: 1;
    color: var(--faint-ink);
    text-align: center;
  }

  .headline {
    margin: 0;
    font-family: "Bebas Neue", Impact, sans-serif;
    font-weight: 400;
    line-height: 1.05;
    color: var(--ink);
  }
  .headline--back { font-size: 13px; }
  .tagline {
    margin: 0;
    font-family: "Bebas Neue", Impact, sans-serif;
    font-weight: 400;
    font-size: 11px;
    line-height: 1;
    white-space: nowrap;
    text-align: center;
    color: var(--ink);
  }
  .contact-row {
    display: grid;
    grid-template-columns: 1fr auto 1fr;
    align-items: center;
    column-gap: 4px;
    font-size: 4px;
    line-height: 1;
    white-space: nowrap;
  }
  .contact-row__left { justify-self: start; }
  .contact-row__right { justify-self: end; }
  .brand-mark {
    display: flex;
    flex-direction: column;
    align-items: center;
    gap: 1px;
    font-family: "Bebas Neue", Impact, sans-serif;
    font-size: 4.5px;
    line-height: 1;
  }
  .brand-mark__dot {
    width: 7px;
    height: 7px;
    border-radius: 50%;
    background: var(--ink);
  }
  .contact-vertical {
    writing-mode: vertical-rl;
    transform: rotate(180deg);
    font-size: 3.8px;
    line-height: 1;
    white-space: nowrap;
    display: flex;
    justify-content: space-between;
  }
  .brand-stack {
    display: flex;
    flex-direction: column;
    align-items: center;
    gap: 3px;
  }
  .brand-stack__circle {
    width: 26px;
    height: 26px;
    border-radius: 50%;
    background: var(--ink);
  }
  .brand-stack__name {
    font-family: "Bebas Neue", Impact, sans-serif;
    font-size: 8px;
    line-height: 1;
    text-align: center;
  }
</style>
</head>
<body>
<main class="board">

  <h2 class="section-title section-title--back">Choose Back</h2>
  <h2 class="section-title section-title--front">Choose Front</h2>

  <!-- Back option 1: photo column -->
  <section class="card" style="left:91px;top:17px;width:229px;height:176px;">
    <div class="emblem" style="left:78px;top:28px;width:130px;height:130px;">
      <span class="emblem__circle"></span>
      <span class="emblem__name">The Kingfisher's Perch</span>
    </div>
    <div class="photo photo--sunset" role="img" aria-label="Sunset sky over trees" style="left:7px;top:7px;width:69px;height:53px;"></div>
    <div class="photo photo--lounge" role="img" aria-label="Living room interior" style="left:7px;top:65px;width:69px;height:49px;"></div>
    <div class="photo photo--bedroom" role="img" aria-label="Bedroom interior" style="left:7px;top:119px;width:69px;height:50px;"></div>
    <div class="stamp-box" style="left:179px;top:16px;"></div>
    <div class="address-line" style="left:154px;top:141px;width:56px;"></div>
    <div class="address-line" style="left:154px;top:149px;width:56px;"></div>
    <div class="address-line" style="left:154px;top:157px;width:56px;"></div>
  </section>

  <!-- Back option 2: buzz message -->
  <section class="card" style="left:333px;top:17px;width:227px;height:176px;">
    <div class="emblem" style="left:70px;top:22px;width:135px;height:135px;">
      <span class="emblem__circle"></span>
      <span class="emblem__name">The Kingfisher's Perch</span>
    </div>
    <h3 class="headline headline--back" style="left:13px;top:20px;width:110px;">Come see what all<br>of the buzz is about</h3>
    <div class="signature-line" style="left:13px;top:56px;width:55px;"></div>
    <div class="writing-lines" style="left:13px;top:64px;width:95px;height:99px;"></div>
    <div class="stamp-box" style="left:179px;top:16px;"></div>
    <div class="address-line" style="left:155px;top:128px;width:55px;"></div>
    <div class="address-line" style="left:155px;top:136px;width:55px;"></div>
    <div class="address-line" style="left:155px;top:144px;width:55px;"></div>
  </section>

  <!-- Back option 3: cottage photo panel -->
  <section class="card" style="left:93px;top:205px;width:227px;height:175px;">
    <div class="photo photo--house" role="img" aria-label="Green cottage exterior with garden" style="left:0;top:0;width:94px;height:175px;"></div>
    <div class="stamp-box" style="left:180px;top:16px;"></div>
    <div class="address-line" style="left:156px;top:142px;width:55px;"></div>
    <div class="address-line" style="left:156px;top:150px;width:55px;"></div>
    <div class="address-line" style="left:156px;top:157px;width:55px;"></div>
  </section>

  <!-- Back option 4: emblem only -->
  <section class="card" style="left:335px;top:205px;width:228px;height:175px;">
    <div class="emblem" style="left:8px;top:20px;width:140px;height:140px;">
      <span class="emblem__circle"></span>
      <span class="emblem__name">The Kingfisher's Perch</span>
    </div>
    <div class="stamp-box" style="left:181px;top:15px;"></div>
    <div class="address-line" style="left:157px;top:128px;width:55px;"></div>
    <div class="address-line" style="left:157px;top:136px;width:55px;"></div>
    <div class="address-line" style="left:157px;top:144px;width:55px;"></div>
  </section>

  <!-- Back option 5: tagline with contact strip -->
  <section class="card" style="left:93px;top:393px;width:225px;height:175px;">
    <h3 class="headline headline--back" style="left:13px;top:15px;width:120px;font-size:11px;">The Kingfisher's Perch<br>– the finest perch on the ridge!</h3>
    <div class="signature-line" style="left:13px;top:48px;width:55px;"></div>
    <div class="writing-lines" style="left:13px;top:52px;width:105px;height:97px;"></div>
    <div class="contact-vertical" style="left:134px;top:10px;height:156px;">
      <span>www.klwtstays.example/417294</span>
      <span>www.chatterly.example/thefinestperchontheridge</span>
    </div>
    <div class="brand-stack" style="left:153px;top:62px;width:60px;">
      <span class="brand-stack__circle"></span>
      <span class="brand-stack__name">The Kingfisher's Perch</span>
    </div>
    <div class="stamp-box" style="left:178px;top:16px;"></div>
    <div class="address-line" style="left:153px;top:132px;width:56px;"></div>
    <div class="address-line" style="left:153px;top:140px;width:56px;"></div>
    <div class="address-line" style="left:153px;top:148px;width:56px;"></div>
  </section>

  <!-- Front option A: six-photo grid -->
  <section class="card" style="left:698px;top:22px;width:226px;height:173px;">
    <div class="photo photo--meadow" role="img" aria-label="Lawn and hills under a rainbow" style="left:7px;top:13px;width:68px;height:51px;"></div>
    <div class="photo photo--lounge" role="img" aria-label="Living room interior" style="left:79px;top:13px;width:66px;height:51px;"></div>
    <div class="photo photo--garden" role="img" aria-label="Garden with evergreen trees" style="left:149px;top:13px;width:70px;height:51px;"></div>
    <div class="photo photo--balloons" role="img" aria-label="Hot air balloons over fields" style="left:7px;top:68px;width:68px;height:51px;"></div>
    <div class="photo photo--autumn" role="img" aria-label="Autumn trees along a trail" style="left:79px;top:68px;width:66px;height:51px;"></div>
    <div class="photo photo--house" role="img" aria-label="Green cottage exterior" style="left:149px;top:68px;width:70px;height:51px;"></div>
    <p class="tagline" style="left:0;top:131px;width:226px;">The Kingfisher's Perch – the finest perch on the ridge!</p>
    <div class="contact-row" style="left:7px;top:148px;width:212px;">
      <span class="contact-row__left">www.klwtstays.example/417294</span>
      <span class="brand-mark"><span class="brand-mark__dot"></span>The Kingfisher's Perch</span>
      <span class="contact-row__right">www.chatterly.example/thefinestperchontheridge</span>
    </div>
  </section>

  <!-- Front option B: nine-photo grid -->
  <section class="card" style="left:942px;top:22px;width:225px;height:171px;">
    <div class="photo photo--lounge" role="img" aria-label="Dining area interior" style="left:6px;top:8px;width:68px;height:51px;"></div>
    <div class="photo photo--bedroom" role="img" aria-label="Bedroom interior" style="left:77px;top:8px;width:68px;height:51px;"></div>
    <div class="photo photo--sunset" role="img" aria-label="Sunset sky over trees" style="left:149px;top:8px;width:71px;height:51px;"></div>
    <div class="photo photo--meadow" role="img" aria-label="Lawn and hills under a rainbow" style="left:6px;top:63px;width:68px;height:51px;"></div>
    <div class="photo photo--lounge" role="img" aria-label="Living room interior" style="left:77px;top:63px;width:68px;height:51px;"></div>
    <div class="photo photo--garden" role="img" aria-label="Garden with evergreen trees" style="left:149px;top:63px;width:71px;height:51px;"></div>
    <div class="photo photo--balloons" role="img" aria-label="Hot air balloons over fields" style="left:6px;top:117px;width:68px;height:51px;"></div>
    <div class="photo photo--autumn" role="img" aria-label="Autumn trees along a trail" style="left:77px;top:117px;width:68px;height:51px;"></div>
    <div class="photo photo--house" role="img" aria-label="Green cottage exterior" style="left:149px;top:117px;width:71px;height:51px;"></div>
  </section>

  <!-- Front option C: single cottage photo -->
  <section class="card" style="left:698px;top:210px;width:226px;height:175px;">
    <div class="photo photo--house" role="img" aria-label="Green cottage exterior with porch" style="left:7px;top:7px;width:212px;height:125px;"></div>
    <p class="tagline" style="left:0;top:139px;width:226px;">The Kingfisher's Perch – the finest perch on the ridge!</p>
    <div class="contact-row" style="left:7px;top:154px;width:212px;">
      <span class="contact-row__left">www.klwtstays.example/417294</span>
      <span class="brand-mark"><span class="brand-mark__dot"></span>The Kingfisher's Perch</span>
      <span class="contact-row__right">www.chatterly.example/thefinestperchontheridge</span>
    </div>
  </section>

  <!-- Front option D: split grid with centre band -->
  <section class="card" style="left:942px;top:210px;width:225px;height:175px;">
    <div class="photo photo--meadow" role="img" aria-label="Lawn and hills under a rainbow" style="left:6px;top:8px;width:68px;height:52px;"></div>
    <div class="photo photo--lounge" role="img" aria-label="Living room interior" style="left:77px;top:8px;width:68px;height:52px;"></div>
    <div class="photo photo--garden" role="img" aria-label="Garden with evergreen trees" style="left:149px;top:8px;width:71px;height:52px;"></div>
    <p class="tagline" style="left:0;top:76px;width:225px;">The Kingfisher's Perch – the finest perch on the ridge!</p>
    <div class="contact-row" style="left:6px;top:91px;width:213px;">
      <span class="contact-row__left">www.klwtstays.example/417294</span>
      <span class="brand-mark"><span class="brand-mark__dot"></span>The Kingfisher's Perch</span>
      <span class="contact-row__right">www.chatterly.example/thefinestperchontheridge</span>
    </div>
    <div class="photo photo--balloons" role="img" aria-label="Hot air balloons over fields" style="left:6px;top:116px;width:68px;height:52px;"></div>
    <div class="photo photo--autumn" role="img" aria-label="Autumn trees along a trail" style="left:77px;top:116px;width:68px;height:52px;"></div>
    <div class="photo photo--house" role="img" aria-label="Green cottage exterior" style="left:149px;top:116px;width:71px;height:52px;"></div>
  </section>

</main>
</body>
</html>
```